ULMIRA card Technical Architecture

Hello everyone ULMIRA: It is a consulting firm in Architecture and Construction. I require a card duplexing, sober, elegant, classic but not boring. Update 1: Use the following data for the card. Name: Gonzalo Pereda Mauricio Villalta Position: COO Twitter: @ulmiraAT Homepage: ulmira-example.com home address not include the participation of all thank you.

Target Market(s)

Construction companies, Architects and Consulting Engineers

Industry/Entity Type

Consulting

Contact Information for Business Card

Los campos que debe tener:
Nombre, Cargo, email, homepage y twitter

Font styles to use
Serif
Sans Serif
Other font styles liked:
• Me gustan playfair display, open sans y roboto, pero estoy sujeto a sus propuestas

Requirements
Must have
• Colors: Present combined proposals in white, red, gray and black Update 1: The two names must be clearly differentiated from the two surnames
Nice to have
• They are free to present their best proposals. I will bring them immediate feedback to the extent you can go see their designs. Complete data for card and logo files will give the winner the

```html
<!DOCTYPE html>
<html lang="es">
<head>
<meta charset="utf-8">
<title>ULMIRA – Tarjeta de presentación</title>
<link rel="stylesheet" href="https://fonts.googleapis.com/css2?family=Montserrat:wght@400;500&family=Open+Sans:wght@400;600;700&display=swap">
<style>
  :root {
    --backdrop: #e8e6e3;
    --card-white: #ffffff;
    --brand-red: #bf0000;
    --accent-red: #b3141c;
    --ink-black: #111111;
    --rule-gray: #c9c9c9;
    --text-white: #ffffff;
  }
  * { margin: 0; padding: 0; box-sizing: border-box; }
  html, body {
    width: 1200px;
    height: 900px;
    overflow: hidden;
    background: var(--backdrop);
  }
  .business-card {
    position: absolute;
    left: 150px;
    top: 172px;
    width: 900px;
    height: 555px;
    background: var(--card-white);
    overflow: hidden;
    box-shadow: 0 6px 24px rgba(0, 0, 0, 0.12);
  }
  .decor-field {
    position: absolute;
    inset: 0;
    background: linear-gradient(165deg, var(--card-white) 0%, var(--card-white) 42%, var(--brand-red) 54%, var(--brand-red) 100%);
  }

  .brand-block {
    position: absolute;
    left: 51px;
    top: 170px;
    width: 380px;
    text-align: center;
  }
  .brand-name {
    font-family: "Montserrat", sans-serif;
    font-weight: 400;
    font-size: 45px;
    line-height: 1;
    letter-spacing: 0.24em;
    margin-right: -0.24em;
    color: var(--ink-black);
  }
  .brand-rule {
    height: 1px;
    background: var(--rule-gray);
    margin: 8px 0 6px;
  }
  .brand-tagline {
    font-family: "Montserrat", sans-serif;
    font-weight: 500;
    font-size: 15.5px;
    letter-spacing: 0.2em;
    margin-right: -0.2em;
    color: var(--accent-red);
  }

  .contact-block {
    position: absolute;
    right: 52px;
    top: 278px;
    text-align: right;
    font-family: "Open Sans", sans-serif;
    color: var(--text-white);
  }
  .person-name {
    font-weight: 700;
    font-size: 29px;
    line-height: 36px;
    margin-right: 27px;
  }
  .person-title {
    font-weight: 400;
    font-size: 22px;
    line-height: 30px;
    margin-right: 27px;
    margin-bottom: 26px;
  }
  .contact-list { list-style: none; }
  .contact-item {
    display: flex;
    justify-content: flex-end;
    align-items: center;
    gap: 13px;
    font-size: 21.5px;
    line-height: 33px;
  }
  .contact-icon {
    width: 16px;
    height: 16px;
    flex: none;
    fill: var(--text-white);
  }
  .social-mark {
    width: 14px;
    height: 14px;
    flex: none;
    margin: 0 1px;
    background: var(--text-white);
    border-radius: 2px;
  }
</style>
</head>
<body>
  <main class="business-card" aria-label="Tarjeta de presentación ULMIRA">
    <div class="decor-field" role="img" aria-label="Decorative red and black wave band across the lower card"></div>

    <header class="brand-block">
      <div class="brand-name">ULMIRA</div>
      <div class="brand-rule"></div>
      <div class="brand-tagline">ARQUITECTURA TÉCNICA</div>
    </header>

    <section class="contact-block">
      <div class="person-name">Tomás Lindqvist</div>
      <div class="person-title">Managing Director</div>
      <ul class="contact-list">
        <li class="contact-item">
          <span>044-555 010 203</span>
          <svg class="contact-icon" viewBox="0 0 16 16" aria-hidden="true"><path d="M3.2 1.2 5.6 1l1.3 3.4-1.6 1.2c.8 1.8 2.3 3.3 4.1 4.1l1.2-1.6 3.4 1.3-.2 2.4c-.1.9-.9 1.5-1.8 1.5C6.4 13.1 2.9 9.6 1.7 3c0-.9.6-1.7 1.5-1.8Z"/></svg>
        </li>
        <li class="contact-item">
          <span>info@ulmira-mail.com</span>
          <svg class="contact-icon" viewBox="0 0 16 16" aria-hidden="true"><path d="M2 4h12v.6L8 9 2 4.6Z"/><path d="M2 5.8 8 10.2l6-4.4V12H2Z"/></svg>
        </li>
        <li class="contact-item">
          <span>www.ulmira-example.com</span>
          <svg class="contact-icon" viewBox="0 0 16 16" aria-hidden="true"><circle cx="8" cy="8" r="6.2" fill="none" stroke="#fff" stroke-width="1.4"/><ellipse cx="8" cy="8" rx="2.6" ry="6.2" fill="none" stroke="#fff" stroke-width="1.2"/><path d="M1.8 8h12.4" stroke="#fff" stroke-width="1.2"/></svg>
        </li>
        <li class="contact-item">
          <span>www.socialsample.com</span>
          <span class="social-mark" aria-hidden="true"></span>
        </li>
      </ul>
    </section>
  </main>
</body>
</html>
```